Moravel Aesthetic Doctor

I require an elegant, luxurious looking business card for my aesthetic business. I am a doctor and that will set me aside from competitors. I am planning to provide home and spa based treatments to clients with high expectations. I have attached my logo.

```html
<!DOCTYPE html>
<html lang="en">
<head>
<meta charset="UTF-8">
<title>Moravel Aesthetic Doctor – Business Card</title>
<link href="https://fonts.googleapis.com/css2?family=Roboto:wght@300;400&display=swap" rel="stylesheet">
<style>
  :root {
    --backdrop: #c9cacc;
    --blue-light: #4fa6dc;
    --blue-deep: #0a63a8;
    --band-grey: #9da3ab;
    --card-white: #f6f6f7;
    --card-grey: #e4e5e8;
    --ink: #2c2f34;
    --muted-ink: #7d8593;
    --accent: #3e9ad6;
    --rule: #9aa0a8;
  }
  * { margin: 0; padding: 0; box-sizing: border-box; }
  html, body {
    width: 1200px; height: 576px; overflow: hidden;
    background: var(--backdrop);
    font-family: "Roboto", Arial, sans-serif;
  }
  .canvas { position: relative; width: 1200px; height: 576px; }

  .card {
    position: absolute; top: 138px; width: 484px; height: 294px;
    border-radius: 12px; overflow: hidden;
    box-shadow: 0 3px 6px rgba(0,0,0,0.25);
  }
  .card--front {
    left: 82px;
    background: linear-gradient(160deg, var(--blue-light) 0%, #2a86c8 45%, var(--blue-deep) 100%);
  }
  .card--back {
    left: 602px; width: 481px; height: 292px;
    background: linear-gradient(135deg, var(--card-white) 0%, var(--card-grey) 100%);
  }

  .brand { position: absolute; display: flex; align-items: center; gap: 22px; }
  .brand__mark {
    width: 94px; height: 94px; border-radius: 50%;
    border: 3px solid currentColor; flex: none;
  }
  .brand__name { font-weight: 300; line-height: 1; }
  .brand__title { display: block; font-size: 50px; letter-spacing: 1px; }
  .brand__subtitle { display: block; font-size: 21px; letter-spacing: 1.5px; margin-top: 6px; }

  .card--front .brand { left: 52px; top: 52px; color: #ffffff; }
  .card--back .brand { left: 26px; top: 28px; color: var(--muted-ink); }

  .services {
    position: absolute; left: 0; right: 0; top: 200px;
    color: #e8f2fa; font-size: 13.5px; text-align: center; line-height: 19px;
  }
  .services .sep { margin: 0 8px; }

  .tagline-band {
    position: absolute; left: 0; right: 0; top: 245px; height: 24px;
    background: var(--band-grey);
    color: #ffffff; font-size: 13px; letter-spacing: 1px;
    display: flex; align-items: center; justify-content: center;
  }

  .doctor { position: absolute; left: 24px; top: 193px; right: 34px; }
  .doctor__line { display: flex; align-items: baseline; gap: 6px; }
  .doctor__name { font-size: 19px; color: var(--ink); white-space: nowrap; }
  .doctor__letters { font-size: 10.5px; color: var(--accent); white-space: nowrap; }
  .doctor__rule { flex: 1; height: 1px; background: var(--rule); margin-left: 4px; }
  .doctor__qualification { font-size: 12.5px; color: var(--accent); margin-top: 5px; }

  .contacts {
    position: absolute; left: 24px; top: 242px;
    display: flex; align-items: center; gap: 8px;
    font-size: 12px; color: var(--ink); white-space: nowrap;
  }
  .contact { display: flex; align-items: center; gap: 5px; }
  .contact__icon { width: 18px; height: 18px; flex: none; }
  .contact .highlight { color: var(--accent); }

  .social-tab {
    position: absolute; right: 0; top: 242px; width: 74px; height: 19px;
    background: var(--accent); border-radius: 10px 0 0 10px;
    display: flex; align-items: center; padding-left: 16px; gap: 6px;
  }
  .social-tab__dot { width: 9px; height: 9px; border-radius: 50%; background: #ffffff; }
</style>
</head>
<body>
<main class="canvas">

  <section class="card card--front" aria-label="Card front">
    <div class="brand">
      <span class="brand__mark"></span>
      <span class="brand__name">
        <span class="brand__title">MORAVEL</span>
        <span class="brand__subtitle">AESTHETIC DOCTOR</span>
      </span>
    </div>
    <p class="services">
      Dermal Injectables<span class="sep">|</span>Plasma Facials<span class="sep">|</span>Microneedling<br>
      Skin Boosters<span class="sep">|</span>Excessive Sweating
    </p>
    <div class="tagline-band">HOME AND SPA BASED TREATMENTS</div>
  </section>

  <section class="card card--back" aria-label="Card back">
    <div class="brand">
      <span class="brand__mark"></span>
      <span class="brand__name">
        <span class="brand__title">MORAVEL</span>
        <span class="brand__subtitle">AESTHETIC DOCTOR</span>
      </span>
    </div>

    <div class="doctor">
      <div class="doctor__line">
        <span class="doctor__name">Dr Elise Varnow</span>
        <span class="doctor__letters">MRCPCH MD</span>
        <span class="doctor__rule"></span>
      </div>
      <p class="doctor__qualification">Australasian Diploma of Aesthetic Medicine</p>
    </div>

    <div class="contacts">
      <span class="contact">
        <svg class="contact__icon" viewBox="0 0 18 18" aria-hidden="true">
          <circle cx="9" cy="9" r="8.3" fill="none" stroke="#c3c7cd"/>
          <path d="M6 4.8c.5-.3 1-.2 1.3.3l.8 1.4c.2.4.1.8-.2 1.1l-.6.5c.4.9 1.1 1.7 2 2.2l.6-.5c.3-.3.8-.3 1.1 0l1.3.9c.4.3.5.9.1 1.3l-.6.6c-.6.6-1.6.6-2.6 0-1.7-1-3-2.5-3.800-4.2-.4-1-.3-1.9.3-2.4z" fill="var(--accent)"/>
        </svg>
        0800 447 315
      </span>
      <span class="contact">
        <svg class="contact__icon" viewBox="0 0 18 18" aria-hidden="true">
          <circle cx="9" cy="9" r="8.3" fill="none" stroke="#c3c7cd"/>
          <rect x="4.5" y="6" width="9" height="6.2" rx="0.8" fill="var(--accent)"/>
          <path d="M4.8 6.4 9 9.5l4.2-3.1" fill="none" stroke="#ffffff" stroke-width="0.9"/>
        </svg>
        elise@moravel.co.nz
      </span>
      <span class="contact">
        <svg class="contact__icon" viewBox="0 0 18 18" aria-hidden="true">
          <circle cx="9" cy="9" r="8.3" fill="none" stroke="#c3c7cd"/>
          <g fill="none" stroke="var(--accent)" stroke-width="0.9">
            <circle cx="9" cy="9" r="4.6"/>
            <ellipse cx="9" cy="9" rx="2" ry="4.6"/>
            <path d="M4.4 9h9.2"/>
          </g>
        </svg>
        <span>www.<span class="highlight">moravel</span>.co.nz</span>
      </span>
    </div>

    <div class="social-tab" aria-label="Social media">
      <span class="social-tab__dot"></span>
      <span class="social-tab__dot"></span>
    </div>
  </section>

</main>
</body>
</html>
```